Quimbly Needs a 1 Page Redesign with UI/UX Elements

Quimbly is a GIF creation and sharing site. We are upgrading one of our main responsive website pages. [Please see: http://quimblyzone.net/R-4TzLa for an example]

Need design versions for Desktop, tablet & mobile.

Also need frontend development to implement page. Currently on Foundation framework.

There are many functions/nav elements that need to be on this page in an uncluttered and clear manner. Not all of functions need to be shown at all times. Need a designer with UI/UX background to incorporate these and make it easy to navigate for the user.

The designer needs to be familiar with the site to understand each function. Color scheme will remain the same as current site.

If there are Dropdowns/collapsed or hidden features - need to know how they look when opened.

Target Market(s)

Quimbly has a varied demographic but focuses on under 25.

Coding

Coded - Design and coding required

Number of Pages Required

1 page

Font styles to use
Sans Serif

Requirements
Must have
• The top and bottom nav bars must stay the same. We are not redesigning the whole site yet, just that page.
• This page is developed with sharing in mind. Our top 3 actions are highlighted below. Be creative & think about user experience as our #1 priority
• Desktop
•  SOCIAL SHARE BUTTONS Zentrova/Plinkit/Voxmora/Brolendar
•  Download Button
•  Create a GIF Button
• OTHER FEATURES THAT MUST BE INCLUDED
• Share This With Friends pop up
• Title of GIF
• Added XX days ago by XXXX in XXX
• Source
• Thumbs up votes showing numerically (no down vote thumb)
• Total Views
• Embed Links: direct, website, message board, markdown
• NSFW Flag
• MP4 to GIF toggle
• Next arrows to scroll through GIFs
• Scroll thumbnail bar for like GIFs at the bottom of the page
• NEW FEATURES TO IMPLEMENT
• Favorite (bookmark Option)
• LOGGED IN USERS:
• Logged in users also have Private Button & Delete Button
• MOBILE
• We would like to keep the mobile page as minimalist as possible.
• Download button
• Create a GIF button
• Sharing button: Drovanel, Zentrova, Plinkit, Voxmora,
• Share Via SMS
• (Please incorporate the share buttons in a creative & clean way)
• Three dots that would open up to reveal tags
• Thumbnail scroll at bottom for GIFs in the same category
Nice to have
• Be creative with how the page features are laid out. We want it to be easy for users to navigate & clear what actions are there.
Should not have
• Basically anything that is on the page now. The buttons don't look like buttons & there is no drive to any actions (like sharing). Please see attached file for what NOT to do.

```html
<!DOCTYPE html>
<html lang="en">
<head>
<meta charset="utf-8">
<title>Quimbly – Flurbnight</title>
<link href="https://fonts.googleapis.com/css2?family=Ubuntu:wght@400;500&display=swap" rel="stylesheet">
<style>
:root{
  --navy:#0f2436;
  --navy-deep:#0a1a28;
  --navy-line:#1d3447;
  --page:#d3dde4;
  --white:#ffffff;
  --gold:#dcad00;
  --gold-text:#d4a300;
  --ink:#222a30;
  --muted:#8c99a5;
  --green:#7cc242;
  --sky:#2f9fdc;
  --bar:#25292d;
  --bar-text:#8b9095;
}
*{box-sizing:border-box;margin:0;padding:0}
html,body{width:1200px;height:1035px;overflow:hidden}
body{background:var(--page);font-family:'Ubuntu',sans-serif;color:var(--ink);position:relative}
.abs{position:absolute}

/* sidebar */
.sidebar{left:0;top:0;width:240px;height:1035px;background:var(--navy)}
.brand{left:22px;top:16px;display:flex;align-items:center;gap:8px;color:var(--white);font-size:22px;font-weight:500}
.brand-mark{width:24px;height:24px;border:3px solid var(--gold);border-radius:4px}
.menu-icon{left:200px;top:22px;width:19px}
.menu-icon span{display:block;height:3px;background:var(--gold);margin-bottom:3px}
.brand-rule{left:0;top:57px;width:240px;height:3px;background:var(--navy-deep)}
.nav{left:0;top:87px;width:216px}
.nav-item{position:relative;height:56px;margin-left:24px;border-bottom:1px solid var(--navy-line);color:#e6edf2;font-size:13px;line-height:56px;padding-left:55px}
.nav-item.active{background:var(--navy-deep);margin-left:0;padding-left:79px}
.nav-item::after{content:"";position:absolute;right:10px;top:24px;width:7px;height:7px;border-radius:50%;background:var(--green)}
.social-block{left:0;top:420px;width:240px;height:316px;background:#11283b}
.block-head{display:flex;align-items:center;gap:14px;font-size:14px;color:var(--sky)}
.dot-sky{width:14px;height:14px;border-radius:50%;background:var(--sky)}
.count{margin-left:50px;color:#4d6477}
.blurb{font-size:10px;line-height:13px;color:#6f8a9f}
.scroll-track{left:228px;top:440px;width:3px;height:285px;background:#0b1d2c}
.scroll-thumb{left:228px;top:515px;width:3px;height:80px;background:#1f3a52}
.thumb{border:3px solid #e9eef2;border-radius:2px}
.fav-head{left:20px;top:758px;width:190px;display:flex;align-items:center;gap:14px;color:var(--sky);font-size:13px}
.fav-head::after{content:"";margin-left:auto;width:7px;height:7px;border-radius:50%;background:var(--green)}
.heart{width:12px;height:11px}
.fav-rule{left:20px;top:794px;width:196px;height:1px;background:var(--navy-line)}
.bookmark{left:147px;top:963px;font-size:10px;color:#7f95a7;display:flex;align-items:center;gap:6px}

/* top actions */
.btn-top{top:32px;height:30px;border-radius:2px;font-size:11px;display:flex;align-items:center;justify-content:center;gap:8px}
.btn-login{left:934px;width:83px;background:var(--navy);color:var(--white)}
.btn-signup{left:1031px;width:85px;background:var(--gold);color:var(--navy);border:1px solid #c29700}

/* card */
.card{left:310px;top:90px;width:806px;height:632px;background:var(--white);border:1px solid #c4ccd2;border-radius:3px;box-shadow:0 1px 3px rgba(0,0,0,.12)}
.stage{left:321px;top:99px;width:784px;height:328px;background:var(--gold)}
.stage-photo{left:367px;top:99px;width:693px;height:328px;background:radial-gradient(circle at 48% 35%,#e2399a 0,#7a1f6a 18%,#2a1f3a 45%,#1a1c2a 75%)}
.play{left:690px;top:240px}
.gif-title{left:322px;top:440px;font-size:25px;color:var(--gold-text);font-weight:400}
.gif-meta{left:324px;top:473px;font-size:11px}
.gif-meta em{font-style:normal;color:var(--gold-text)}
.stat{font-size:12px;color:var(--gold-text);display:flex;align-items:center;gap:8px}
.rule{left:322px;top:500px;width:774px;height:1px;background:#e3e6e9}
.section-title{font-size:19px;color:var(--gold-text);font-weight:400}
.body-text{font-size:13px;color:#30383e}
.btn-create{left:534px;top:549px;width:204px;height:33px;background:var(--gold);border:1px solid #c89c00;color:#2a2a2a;font-size:13px;display:flex;align-items:center;justify-content:center}
.toggle{left:766px;top:549px;width:140px;height:33px;background:var(--bar);border-radius:2px;padding:3px}
.toggle span{position:absolute;top:3px;height:27px;width:62px;font-size:13px;display:flex;align-items:center;justify-content:center}
.toggle .off{left:4px;color:var(--gold)}
.toggle .on{left:71px;background:var(--gold);color:var(--navy);border-radius:2px}
.links{left:330px;top:614px;display:flex;gap:12px;font-size:13px;color:#30383e}
.links i{font-style:normal;color:var(--gold)}
.card-sep{left:311px;top:665px;width:804px;height:4px;background:#eef0f2}

/* action bar */
.action-bar{left:310px;top:670px;width:806px;height:52px;background:var(--bar);border-bottom:3px solid var(--gold);border-radius:0 0 3px 3px}
.share-tray{left:310px;top:670px;width:162px;height:52px;background:var(--gold);border-radius:0 0 0 3px}
.share-chips{left:330px;top:684px;display:flex;border-radius:3px;overflow:hidden}
.share-chips span{width:25px;height:26px;display:block}
.action{top:670px;height:49px;display:flex;align-items:center;gap:8px;font-size:14px;color:var(--bar-text)}
.action-div{top:674px;width:1px;height:44px;background:#3a3f44}

/* related */
.related-title{left:318px;top:766px;font-size:16px;color:#2b3238;font-weight:400}
.dash{left:318px;top:800px;width:792px;border-top:1px dashed #5a6168}
.rel{top:822px;width:183px;height:111px;border:2px solid #f4f6f7;box-shadow:0 1px 3px rgba(0,0,0,.3)}
.footer-rule{left:310px;top:991px;width:813px;height:1px;background:#bfc8cf}
.footer{left:912px;top:1005px;font-size:11px;color:#2b3238}
</style>
</head>
<body>

<aside class="abs sidebar"></aside>
<div class="abs brand"><span class="brand-mark"></span>Quimbly</div>
<div class="abs menu-icon"><span></span><span></span><span></span></div>
<div class="abs brand-rule"></div>

<nav class="abs nav">
  <div class="nav-item active">The Gallery</div>
  <div class="nav-item">Pictures to Gif</div>
  <div class="nav-item">Streamvo to Gif</div>
  <div class="nav-item">Upload a Gif</div>
  <div class="nav-item">Video to Gif</div>
  <div class="nav-item">Webcam to Gif</div>
</nav>

<section class="abs social-block"></section>
<div class="abs block-head" style="left:26px;top:436px"><span class="dot-sky"></span>Plinkit<span class="count">17</span></div>
<p class="abs blurb" style="left:25px;top:466px;width:190px">Lorem ipsum dolor sit amet, consectetur adipiscing elit..</p>
<div class="abs scroll-track"></div><div class="abs scroll-thumb"></div>
<div class="abs thumb" role="img" aria-label="Friends laughing together" style="left:24px;top:508px;width:80px;height:94px;background:linear-gradient(135deg,#c9b08e,#e8d6c0 50%,#7a9fb4)"></div>
<div class="abs thumb" role="img" aria-label="Children playing by the sea" style="left:124px;top:508px;width:80px;height:94px;background:linear-gradient(135deg,#5fa6d6,#d9b082 55%,#e3c43a)"></div>
<div class="abs thumb" role="img" aria-label="Family outdoors in a park" style="left:24px;top:620px;width:80px;height:94px;background:linear-gradient(160deg,#dfe6ea,#b59678 50%,#5e7a3a)"></div>
<div class="abs thumb" role="img" aria-label="Mother and child with flowers" style="left:124px;top:620px;width:80px;height:94px;background:linear-gradient(160deg,#e5e2dc,#d6b59a 50%,#d94b7a)"></div>

<div class="abs fav-head"><svg class="heart" viewBox="0 0 12 11"><path d="M6 11 1 6C-1 4 0 0 3 0c1.5 0 2.5 1 3 2 .5-1 1.5-2 3-2 3 0 4 4 2 6z" fill="#2f9fdc"/></svg>Favorite</div>
<div class="abs fav-rule"></div>
<div class="abs thumb" role="img" aria-label="Couple smiling" style="left:22px;top:809px;width:55px;height:47px;background:linear-gradient(135deg,#c29a7a,#eee2d6)"></div>
<div class="abs thumb" role="img" aria-label="Friends posing" style="left:90px;top:809px;width:56px;height:47px;background:linear-gradient(135deg,#a8a39a,#e3ddd3)"></div>
<div class="abs thumb" role="img" aria-label="Woman laughing" style="left:159px;top:809px;width:55px;height:47px;background:linear-gradient(135deg,#e1c9a3,#b48a5e)"></div>
<div class="abs thumb" role="img" aria-label="Group picnic" style="left:22px;top:869px;width:55px;height:47px;background:linear-gradient(135deg,#d8c7a4,#e6b04c)"></div>
<div class="abs thumb" role="img" aria-label="Friends hugging" style="left:90px;top:869px;width:56px;height:47px;background:linear-gradient(135deg,#7a6a5c,#c78c88)"></div>
<div class="abs thumb" role="img" aria-label="Group on a lawn" style="left:159px;top:869px;width:55px;height:47px;background:linear-gradient(180deg,#8aa0b4,#4a5a4a 60%,#5f9a3a)"></div>
<p class="abs blurb" style="left:22px;top:933px;width:195px">Lorem ipsum dolor sit amet, consectetur adipiscing elit..</p>
<div class="abs bookmark"><svg width="6" height="8" viewBox="0 0 6 8"><path d="M0 0h6v8L3 6 0 8z" fill="#7f95a7"/></svg>Book Mark</div>

<div class="abs btn-top btn-login"><svg width="8" height="10" viewBox="0 0 8 10"><path d="M2 4V3a2 2 0 0 1 4 0v1h1v6H1V4zm1 0h2V3a1 1 0 0 0-2 0z" fill="#fff"/></svg>Log in</div>
<div class="abs btn-top btn-signup"><svg width="10" height="10" viewBox="0 0 10 10"><circle cx="5" cy="3" r="2.5" fill="#0f2436"/><path d="M0 10c0-3 2-4.5 5-4.5S10 7 10 10z" fill="#0f2436"/></svg>Sign up</div>

<main class="abs card"></main>
<div class="abs stage"></div>
<div class="abs stage-photo" role="img" aria-label="Friends celebrating at a party with confetti"></div>
<svg class="abs" style="left:334px;top:248px" width="16" height="28" viewBox="0 0 16 28"><path d="M13 2 3 14l10 12" stroke="#b48a00" stroke-width="4" fill="none"/></svg>
<svg class="abs" style="left:1074px;top:248px" width="16" height="28" viewBox="0 0 16 28"><path d="M3 2l10 12L3 26" stroke="#b48a00" stroke-width="4" fill="none"/></svg>
<svg class="abs play" width="46" height="46" viewBox="0 0 46 46"><circle cx="23" cy="23" r="22" fill="#1c1c1c" stroke="#fff" stroke-width="2"/><path d="M17 12v22l19-11z" fill="#fff"/></svg>

<h1 class="abs gif-title">Flurbnight</h1>
<p class="abs gif-meta">Added last week <em>anonymously in funny gifs</em></p>
<div class="abs stat" style="left:1040px;top:453px"><svg width="12" height="12" viewBox="0 0 12 12"><path d="M1 5h2v6H1zM4 5l3-4c1 0 1.5.7 1.2 1.8L7.8 4.5H11c.6 0 1 .5.9 1.1l-1 4.5c-.1.5-.5.9-1 .9H4z" fill="none" stroke="#d4a300"/></svg>233</div>
<div class="abs stat" style="left:970px;top:473px"><svg width="12" height="8" viewBox="0 0 12 8"><path d="M0 4q6-8 12 0-6 8-12 0z" fill="#d4a300"/><circle cx="6" cy="4" r="1.6" fill="#fff"/></svg>1415 Total Views</div>
<div class="abs rule"></div>

<h2 class="abs section-title" style="left:326px;top:521px">Sources</h2>
<p class="abs body-text" style="left:327px;top:555px">Watch the full Streamvo video</p>
<div class="abs btn-create">Create GIF from this video</div>
<div class="abs toggle"><span class="off">MP4</span><span class="on">GIF</span></div>
<h2 class="abs section-title" style="left:329px;top:582px">Links</h2>
<div class="abs links">Direct <i>|</i> Website <i>|</i> Message Board <i>|</i> Markdown</div>
<div class="abs card-sep"></div>

<div class="abs action-bar"></div>
<div class="abs share-tray"></div>
<div class="abs share-chips">
  <span style="background:#3f66b0" title="Zentrova" aria-label="Zentrova"></span>
  <span style="background:#4c4c4c" title="Gloomix" aria-label="Gloomix"></span>
  <span style="background:#2aa3e0" title="Plinkit" aria-label="Plinkit"></span>
  <span style="background:#3b91c8" title="Linkora" aria-label="Linkora"></span>
  <span style="background:#29a8e6" title="Voxmora" aria-label="Voxmora"></span>
</div>
<div class="abs action" style="left:518px"><svg width="14" height="11" viewBox="0 0 14 11"><path d="M8 0l6 5-6 5V7C4 7 2 8 0 11 1 6 3 3.5 8 3z" fill="#8b9095"/></svg>Share</div>
<div class="abs action-div" style="left:632px"></div>
<div class="abs action" style="left:667px"><svg width="16" height="15" viewBox="0 0 16 15"><path d="M6 0h4v6h3l-5 5-5-5h3zM0 11h2v2h12v-2h2v4H0z" fill="#8b9095"/></svg>Download</div>
<div class="abs action-div" style="left:794px"></div>
<div class="abs action" style="left:836px"><svg width="13" height="13" viewBox="0 0 13 13"><rect width="5.5" height="5.5" fill="#8b9095"/><rect x="7.5" width="5.5" height="5.5" fill="#8b9095"/><rect y="7.5" width="5.5" height="5.5" fill="#8b9095"/><rect x="7.5" y="7.5" width="5.5" height="5.5" fill="#8b9095"/></svg>More</div>
<div class="abs action-div" style="left:954px"></div>
<div class="abs action" style="left:984px"><svg width="20" height="17" viewBox="0 0 20 17"><path d="M5 0h15v10h-3v3l-3-3H5z" fill="#8b9095"/><path d="M0 5h4v6h8v2H6l-3 3v-3H0z" fill="#8b9095"/></svg>Create a Gif</div>

<h2 class="abs related-title">Check out these funny gifs</h2>
<div class="abs dash"></div>
<svg class="abs" style="left:287px;top:866px" width="14" height="22" viewBox="0 0 14 22"><path d="M11 2 3 11l8 9" stroke="#1c2a36" stroke-width="3" fill="none"/></svg>
<div class="abs rel" role="img" aria-label="Man lifting a barbell in a gym" style="left:317px;background:linear-gradient(180deg,#5d5a52,#8a8a86 50%,#3c3a36)"></div>
<div class="abs rel" role="img" aria-label="Woman under a rainbow" style="left:519px;background:linear-gradient(180deg,#f1eee9,#e8c9a0 50%,#b88c70)"></div>
<div class="abs rel" role="img" aria-label="Man in a classic space drama scene" style="left:722px;background:radial-gradient(circle at 50% 55%,#b47a5a,#3a2e2a 55%,#141416)"></div>
<div class="abs rel" role="img" aria-label="Young man looking into a webcam" style="left:925px;background:linear-gradient(135deg,#c8ccc8,#8a7060 50%,#2a2624)"></div>
<svg class="abs" style="left:1123px;top:866px" width="14" height="22" viewBox="0 0 14 22"><path d="M3 2l8 9-8 9" stroke="#1c2a36" stroke-width="3" fill="none"/></svg>

<div class="abs footer-rule"></div>
<p class="abs footer">©2015 Hubnest | All rights reserved</p>

</body>
</html>
```